Velvet Riot Rising Line of Sparkling Wine & Spirits

Back info: Nora Beth Quill Owner 555-318-4402 1480 E. Harlow Ave, Bldg. 2, & 3, Elmridge Vale 95871
Sparkling Wines & Memorabilia www.velvetriotrising.com
Ok I have uploaded the winning design. The color that I am after is the Fushia, Raspberry, Red, Matte Satin Matalic Finish. With a 24 Karet Gold color Foil. The Bottle is on the top row and it's the 2nd Bottle in. That is the Color that I want. This is the style of font. Make sure that you put what we're advertising. Good Luck to you all. Warmest regards, Nora
21 & up UniSex
Sparkling Wine and Memorabilia
there listed up above.....

```html
<!DOCTYPE html>
<html lang="en">
<head>
<meta charset="utf-8">
<title>Velvet Riot Rising – Business Card</title>
<link rel="stylesheet" href="https://fonts.googleapis.com/css2?family=Marcellus&family=Montserrat:wght@400;500&display=swap">
<style>
  :root {
    --fuchsia: #dc1489;
    --fuchsia-deep: #9e0f5e;
    --fuchsia-edge: #7d0c4a;
    --gold: #d6a93a;
    --gold-light: #f0d27a;
    --gold-dark: #a57a1c;
    --ink: #1c1416;
    --white: #ffffff;
    --backdrop: #3a3a3c;
  }
  * { margin: 0; padding: 0; box-sizing: border-box; }
  html, body {
    width: 1200px; height: 1200px; overflow: hidden;
    background: var(--backdrop);
  }
  .canvas { position: relative; width: 1200px; height: 1200px; }

  .card {
    position: absolute; left: 190px;
    width: 820px; height: 470px;
    border-radius: 34px; overflow: hidden;
    background: radial-gradient(ellipse at 50% 45%, var(--fuchsia) 0%, #c9127d 45%, var(--fuchsia-deep) 85%, var(--fuchsia-edge) 100%);
    box-shadow: 0 0 0 3px var(--gold), 0 18px 40px rgba(0,0,0,.45);
  }
  .card-front { top: 80px; }
  .card-back { top: 640px; }

  /* Front */
  .contact { position: absolute; left: 56px; top: 64px; color: var(--white); }
  .contact-name {
    font-family: "Marcellus", serif; font-size: 44px; line-height: 1; font-weight: 400;
    color: var(--gold-light);
    background: linear-gradient(180deg, var(--gold-light), var(--gold) 60%, var(--gold-dark));
    -webkit-background-clip: text; background-clip: text; -webkit-text-fill-color: transparent;
  }
  .contact-role { font-family: "Montserrat", sans-serif; font-size: 19px; line-height: 1.2; margin: 4px 0 14px 10px; }
  .contact-list { list-style: none; font-family: "Montserrat", sans-serif; font-size: 17px; line-height: 1.3; }
  .contact-list li { display: flex; align-items: flex-start; gap: 12px; margin-bottom: 8px; }
  .contact-list svg { flex: none; width: 20px; height: 20px; margin-top: 1px; }
  .social { display: flex; gap: 10px; margin: 4px 0 0 40px; }
  .social span { width: 26px; height: 26px; border-radius: 50%; background: var(--gold); }

  .brand { position: absolute; right: 60px; top: 78px; width: 360px; text-align: center; }
  .brand-name {
    font-family: "Marcellus", serif; font-size: 46px; line-height: 1.05;
    color: var(--gold);
  }
  .brand-tagline {
    font-family: "Marcellus", serif; font-size: 20px; letter-spacing: 1px;
    text-transform: uppercase; color: var(--ink); margin-top: 22px; line-height: 1.15;
  }

  .gold-rule {
    position: absolute; left: 0; right: 0; bottom: 120px; height: 12px;
    background: linear-gradient(90deg, var(--gold-dark), var(--gold-light) 45%, var(--gold) 70%, var(--gold-dark));
  }
  .pattern-band {
    position: absolute; left: 0; right: 0; bottom: 0; height: 120px;
    background: linear-gradient(180deg, #5a0f3a, #3a0c28);
  }

  /* Back */
  .back-brand {
    position: absolute; inset: 0; display: flex; align-items: center; justify-content: center;
    font-family: "Marcellus", serif; font-size: 76px; color: var(--ink);
  }
</style>
</head>
<body>
<div class="canvas">

  <section class="card card-front">
    <div class="contact">
      <h1 class="contact-name">Nora Beth Quill</h1>
      <p class="contact-role">Owner</p>
      <ul class="contact-list">
        <li>
          <svg viewBox="0 0 24 24" fill="#d6a93a"><path d="M6.6 10.8a15 15 0 0 0 6.6 6.6l2.2-2.2a1 1 0 0 1 1-.25 11.4 11.4 0 0 0 3.6.57 1 1 0 0 1 1 1V20a1 1 0 0 1-1 1A17 17 0 0 1 3 4a1 1 0 0 1 1-1h3.5a1 1 0 0 1 1 1c0 1.25.2 2.45.57 3.570a1 1 0 0 1-.25 1z"/></svg>
          <span>555-318-4402</span>
        </li>
        <li>
          <svg viewBox="0 0 24 24" fill="none" stroke="#d6a93a" stroke-width="2"><circle cx="12" cy="12" r="9"/><path d="M3 12h18M12 3c3 3.2 3 14.8 0 18M12 3c-3 3.2-3 14.8 0 18"/></svg>
          <span>www.velvetriotrising.com</span>
        </li>
        <li>
          <svg viewBox="0 0 24 24" fill="#d6a93a"><path d="M12 2a7 7 0 0 0-7 7c0 5 7 13 7 13s7-8 7-13a7 7 0 0 0-7-7zm0 9.5A2.5 2.5 0 1 1 12 6.5a2.5 2.5 0 0 1 0 5z"/></svg>
          <span>1480 E. Harlow Ave, Bldg. 2, &amp; 3,<br>Elmridge Vale 95871<br>Sparkling Wines &amp; Memorabilia</span>
        </li>
      </ul>
      <div class="social"><span></span><span></span></div>
    </div>

    <div class="brand">
      <p class="brand-name">Velvet Riot Rising</p>
      <p class="brand-tagline">Line of Sparkling<br>Wine &amp; Spirits</p>
    </div>

    <div class="gold-rule"></div>
    <div class="pattern-band" role="img" aria-label="Decorative lattice pattern in black and fuchsia"></div>
  </section>

  <section class="card card-back">
    <p class="back-brand">Velvet Riot Rising</p>
  </section>

</div>
</body>
</html>
```